Coastal Learner Bureau business cards

Australian company about to start offering its services. We recruit international students to come to study English, vocational education and postgraduate courses in Australia. We help them find the institution and select the right city they want to come to Australia. We are a young, online oriented and supportive agency. Our clients are between 18 and 35 years old, mainly University students, young professionals or people with work experience. We provide much more information that any other agency offer. We administrate a Facebook group with more than 11.000 members that daily ask questions about general information when coming to Australia, while they are here and even after they leave the country

Target Market(s)

International students from South America, Central America and Europe

Industry/Entity Type

Student

Contact Information for Business Card

Tomas Bilbrea
Managing Director
tomas@kelvarin.com.au
www.kelvoria.com.au
+61 491058264
Melbourne, Australia

Font styles to use
Serif
Sans Serif

Colors

Designer to choose colors to be used in the design.

Requirements
Must have
• Horizontal design
• Standard business card size and shape. If font uses green or yellow colours, they will have to match the ones from the logo
Nice to have
• UPDATE: Use the contents of the green image to design one of the card sides. Use our logo in the background of that side as watermark.
• Passport image, or immigration stamps. A picture of the Yarra River (from Melbourne) would be cool as well.
Should not have
• Non-standard business card size and shape
• Not black as the background colour of any sides as we are not a VIP agency or a hight class service. We are orientes to young people and they like colours, pictures, something attractive.
• Vertical design
• NO YELLOW or BLACK AS THE BACKGROUND COLOUR OF ANY SIDE OF THE BIZ CARD

```html
<!DOCTYPE html>
<html lang="en">
<head>
<meta charset="utf-8">
<title>Coastal Learner Bureau business cards</title>
<link rel="stylesheet" href="https://fonts.googleapis.com/css2?family=Roboto:wght@400;500;700&family=Roboto+Condensed:wght@500;700&display=swap">
<style>
  :root {
    --canvas: #2b2b2b;
    --paper: #f2f2f2;
    --green: #155b3c;
    --gold: #e0ad05;
    --white: #ffffff;
    --ink: #444444;
    --mark-green: rgba(21, 91, 60, 0.10);
    --mark-gold: rgba(224, 173, 5, 0.12);
  }
  * { margin: 0; padding: 0; box-sizing: border-box; }
  html, body { width: 1200px; height: 960px; overflow: hidden; }
  body { background: var(--canvas); font-family: "Roboto", Arial, sans-serif; position: relative; }

  .card { position: absolute; width: 600px; height: 343px; background: var(--paper); overflow: hidden; }
  .card--front { left: 314px; top: 113px; }
  .card--back { left: 311px; top: 472px; }

  .brand { position: absolute; display: flex; align-items: center; gap: 10px;
           font-family: "Roboto", Arial, sans-serif; font-weight: 700; color: var(--green); }
  .brand__dot { width: 14px; height: 14px; border-radius: 50%; background: var(--green); }
  .card--front .brand { left: 46px; top: 76px; font-size: 44px; }
  .card--back .brand { left: 410px; top: 210px; font-size: 40px; }

  .front-band { position: absolute; left: 0; top: 0; width: 600px; height: 343px; }

  .holder { position: absolute; left: 40px; top: 270px; }
  .holder__name { font-family: "Roboto Condensed", Arial, sans-serif; font-weight: 700;
                  font-size: 23px; color: var(--gold); letter-spacing: 0.2px; line-height: 26px; }
  .holder__role { font-family: "Roboto", Arial, sans-serif; font-weight: 500; font-size: 15px;
                  color: var(--white); letter-spacing: 0.3px; line-height: 18px; }

  .contact { position: absolute; right: 36px; top: 236px; list-style: none; text-align: right;
             color: var(--white); font-size: 14.5px; line-height: 19.5px; }
  .contact li { display: flex; justify-content: flex-end; align-items: center; gap: 6px; }
  .contact__place { margin-right: 20px; margin-bottom: 4px; }
  .contact svg { width: 13px; height: 13px; flex: none; }

  .watermark { position: absolute; inset: 0;
               background: linear-gradient(135deg, var(--mark-green), var(--mark-gold) 50%, var(--mark-green)); }
  .tagline { position: absolute; left: 417px; top: 295px; font-size: 14.5px; color: var(--ink); }
</style>
</head>
<body>

<section class="card card--front" aria-label="Business card front">
  <div class="brand"><span class="brand__dot"></span>Kelvoria</div>

  <svg class="front-band" viewBox="0 0 600 343" aria-hidden="true">
    <path d="M0,231 H314 C322,231 326,228 330,220" fill="none" stroke="var(--gold)" stroke-width="8"/>
    <path d="M0,241 H316 C327,241 332,236 337,224 C342,214 348,211 362,211 H600 V343 H0 Z" fill="var(--green)"/>
    <path d="M0,239.5 H316 C326,239.5 331,235 336,223" fill="none" stroke="var(--white)" stroke-width="2"/>
  </svg>

  <div class="holder">
    <p class="holder__name">TOMAS BILBREA</p>
    <p class="holder__role">MANAGING DIRECTOR</p>
  </div>

  <ul class="contact">
    <li class="contact__place">Melbourne, Australia</li>
    <li>+61 491058264
      <svg viewBox="0 0 16 16" aria-hidden="true"><path fill="var(--gold)" d="M3.5 1 L6 1 L7 4.5 L5.3 5.8 C6.2 7.8 8.2 9.8 10.2 10.7 L11.5 9 L15 10 L15 12.5 C15 13.9 13.9 15 12.5 15 C6.2 15 1 9.8 1 3.5 C1 2.1 2.1 1 3.5 1 Z"/></svg>
    </li>
    <li>tomas@kelvarin.com.au
      <svg viewBox="0 0 16 16" aria-hidden="true"><rect x="1" y="3" width="14" height="10" rx="1" fill="var(--gold)"/><path d="M1.5 3.8 L8 9 L14.5 3.8" fill="none" stroke="var(--green)" stroke-width="1.4"/></svg>
    </li>
    <li>www.kelvoria.com.au
      <svg viewBox="0 0 16 16" aria-hidden="true"><circle cx="8" cy="8" r="7" fill="var(--gold)"/><path d="M8 1 C5 4 5 12 8 15 M8 1 C11 4 11 12 8 15 M1 8 H15" fill="none" stroke="var(--green)" stroke-width="1.2"/></svg>
    </li>
  </ul>
</section>

<section class="card card--back" aria-label="Business card back">
  <div class="watermark" role="img" aria-label="Faint repeating brand watermark pattern in pale green and gold"></div>
  <div class="brand"><span class="brand__dot"></span>Kelvoria</div>
  <p class="tagline">Hacemos más por ti!</p>
</section>

</body>
</html>
```